Design the Business card for NetVaultic

Business card required for a professional Cyber Security business.
Company Logo and Icon has already been provided however I would like other options for the logo and icon to compare to. Alternatively, please refine/enhance the image of the logo.icon I have already provided.

If you are going to use the provided logo and icon, I was thinking that the company raised Logo on White background would serve well on the front of the card. See attached. AND, a large company raised stand-alone icon to appear on black background on the back of the card with tagline 'Cyber Risk Management, Governance and Consulting' or 'Cyber Security for your Business' See attached.
Alternatively, provide your own design for the logo and icon.

Target Market(s)

Enterprise, Government, Financial.

Contact Information for Business Card

Tavin Orloweth
Founder and CEO

Email Address
Mobile Number
Website URL
LinkedIn URL

Logo Text

NetVaultic - see attached example of logo

Font styles to use
Other font styles liked:
• Berlin Sans FB

Requirements
Must have
• Clean large and bold icon on the back with tagline.
• Horizontal alignment,
Nice to have
• Round edges.
• Raised Logo/Icon
Should not have
• An unprofessional look and feel.

```html
<!DOCTYPE html>
<html lang="en">
<head>
<meta charset="utf-8">
<title>NetVaultic Business Card</title>
<link rel="stylesheet" href="https://fonts.googleapis.com/css2?family=Quicksand:wght@500;600&family=Roboto:wght@400;500&display=swap">
<style>
  :root {
    --backdrop: #3b3330;
    --card: #1b1d21;
    --card-edge: #15161a;
    --brand-blue: #1d80d8;
    --muted-blue: #2d5f99;
    --accent-gold: #e9a91f;
    --ink-light: #f2f3f5;
    --rule: #5a5d63;
  }
  * { box-sizing: border-box; margin: 0; padding: 0; }
  html, body {
    width: 1200px; height: 769px; overflow: hidden;
    background: var(--backdrop);
  }
  .canvas {
    position: relative; width: 1200px; height: 769px;
    display: flex; align-items: center; justify-content: center; gap: 40px;
  }
  .card {
    position: relative; width: 540px; height: 309px;
    background: var(--card);
    border-radius: 12px;
    box-shadow: 0 10px 24px rgba(0,0,0,.45);
    overflow: hidden;
  }
  .brand {
    display: flex; align-items: center; gap: 14px;
    font-family: "Quicksand", sans-serif; font-weight: 600;
    letter-spacing: .5px;
  }
  .brand-dot { border-radius: 50%; flex: none; }

  /* back card */
  .card-back .brand {
    position: absolute; left: 96px; top: 92px;
    color: var(--muted-blue); font-size: 52px;
  }
  .card-back .brand-dot { width: 58px; height: 58px; background: var(--muted-blue); }
  .tagline {
    position: absolute; left: 0; right: 0; top: 196px; text-align: center;
    font-family: "Quicksand", sans-serif; font-weight: 500; font-size: 17px;
    color: var(--muted-blue);
  }
  .tagline .highlight { color: var(--accent-gold); }

  /* front card */
  .card-front .brand {
    position: absolute; left: 150px; top: 62px;
    color: var(--brand-blue); font-size: 48px;
  }
  .card-front .brand-dot { width: 54px; height: 54px; background: var(--brand-blue); }
  .holder {
    position: absolute; right: 292px; top: 190px; text-align: right;
    font-family: "Roboto", sans-serif; font-weight: 500; text-transform: uppercase;
  }
  .holder-name { color: var(--brand-blue); font-size: 17px; letter-spacing: .3px; }
  .holder-role { color: var(--accent-gold); font-size: 14px; margin-top: 4px; }
  .divider {
    position: absolute; left: 268px; top: 180px; width: 1px; height: 86px;
    background: var(--rule);
  }
  .contacts {
    position: absolute; left: 286px; top: 182px; list-style: none;
    font-family: "Roboto", sans-serif; font-size: 14px; color: var(--ink-light);
  }
  .contacts li { display: flex; align-items: center; gap: 9px; height: 21px; }
  .contacts svg { width: 13px; height: 13px; flex: none; }
</style>
</head>
<body>
<main class="canvas">
  <section class="card card-back" aria-label="Card back">
    <div class="brand"><span class="brand-dot"></span>NetVaultic</div>
    <p class="tagline">Cyber Risk Management, <span class="highlight">Governance &amp; Consulting</span></p>
  </section>

  <section class="card card-front" aria-label="Card front">
    <div class="brand"><span class="brand-dot"></span>NetVaultic</div>
    <div class="holder">
      <p class="holder-name">Tavin Orloweth</p>
      <p class="holder-role">Founder &amp; CEO</p>
    </div>
    <span class="divider"></span>
    <ul class="contacts">
      <li>
        <svg viewBox="0 0 12 12" aria-hidden="true"><rect x="3" y="0.5" width="6" height="11" rx="1.2" fill="none" stroke="#1d80d8" stroke-width="1.2"/><circle cx="6" cy="9.5" r=".7" fill="#1d80d8"/></svg>
        555 014 2738
      </li>
      <li>
        <svg viewBox="0 0 12 12" aria-hidden="true"><rect x="0.5" y="2" width="11" height="8" rx="1" fill="#1d80d8"/><path d="M1 2.6 6 6.6 11 2.6" fill="none" stroke="#1b1d21" stroke-width="1"/></svg>
        tavin@netvaultic.com
      </li>
      <li>
        <svg viewBox="0 0 12 12" aria-hidden="true"><circle cx="6" cy="6" r="5.5" fill="#1d80d8"/><path d="M1 6h10M6 .6c2.2 2.6 2.2 8.2 0 10.8M6 .6c-2.2 2.6-2.2 8.2 0 10.8" fill="none" stroke="#1b1d21" stroke-width=".9"/></svg>
        www.netvaultic.com
      </li>
      <li>
        <svg viewBox="0 0 12 12" aria-hidden="true"><circle cx="6" cy="6" r="5.5" fill="#1d80d8"/></svg>
        netvaultic
      </li>
    </ul>
  </section>
</main>
</body>
</html>
```